Year 12 Chemistry Workbook illustrations and diagrams

We are producing a Chemistry Workbook for senior high-school students in South Australia and require a designer to create illustrations including detailed diagrams and graphs for our upcoming publication.

The attached files are illustrations that we'd like to have recreated, with your own personal style incorporated.

We will require you to do the following:
- Create vector artwork
- Supply AI files
- Use the font helvetica neue 45 light, or its italic variation
- Use full colour wherever possible
- Please use 100% black, not RGB black/eye-dropped black

Target Market(s)

Senior high school students

Industry/Entity Type

School

Font styles to use
Sans Serif

Colors

Designer to choose colors to be used in the design.

Requirements
Must have
• - Create vector artwork
• - Supply AI files
• - Use the font helvetica neue 45 light, or its italic variation
• - Use full colour wherever possible
• - Please use 100% black, not RGB black/eye-dropped black
Should not have
• Please do not use RGB black/eye-dropped black

```html
<!DOCTYPE html>
<html lang="en">
<head>
<meta charset="utf-8">
<title>Stages in the production of bioethanol</title>
<link rel="stylesheet" href="https://fonts.googleapis.com/css2?family=Arimo:wght@400;700&display=swap">
<style>
  :root {
    --ink: #000000;
    --cane-light: #8ee3f9;
    --cane-mid: #4cc8ef;
    --corn-yellow: #ecd81f;
    --corn-orange: #ff8000;
    --stage-text: #ffffff;
    --paper: #ffffff;
  }
  html, body {
    margin: 0;
    padding: 0;
    width: 1200px;
    height: 845px;
    overflow: hidden;
    background: var(--paper);
  }
  .figure {
    display: block;
    width: 1200px;
    height: 845px;
    font-family: "Arimo", "Helvetica Neue", Arial, sans-serif;
  }
  .intro, .label, .caption { fill: var(--ink); font-size: 14px; }
  .intro { font-size: 13px; }
  .caption { font-size: 14px; }
  .stage-name { fill: var(--stage-text); font-size: 15px; }
  .feed { font-weight: 700; font-size: 18px; }
  .feed--cane { fill: var(--cane-light); }
  .feed--corn { fill: var(--corn-orange); }
  .product { font-weight: 700; font-size: 16px; }
  .product--cane { fill: var(--cane-light); }
  .product--corn { fill: var(--corn-orange); }
  .fill-cane-light { fill: var(--cane-light); }
  .fill-cane-mid { fill: var(--cane-mid); }
  .fill-corn-yellow { fill: var(--corn-yellow); }
  .fill-corn-orange { fill: var(--corn-orange); }
  .stroke-cane-light { stroke: var(--cane-light); fill: none; stroke-width: 8; }
  .stroke-corn-yellow { stroke: var(--corn-yellow); fill: none; stroke-width: 8; }
</style>
</head>
<body>
<svg class="figure" viewBox="0 0 850 598.5" xmlns="http://www.w3.org/2000/svg" role="img" aria-label="Stages in the production of bioethanol from sugarcane and from dry ground corn">

  <!-- Introduction -->
  <text class="intro" x="140" y="24">The ethanol content is limited by the types of yeast and enzymes present during fermentation.</text>
  <text class="intro" x="140" y="44">Higher concentrations of ethanol are obtained through fractional distillation. (Fig. 4.1.2)</text>

  <!-- Sugarcane route -->
  <g class="route route--cane">
    <text class="feed feed--cane" x="120" y="76">Sugar-</text>
    <text class="feed feed--cane" x="120" y="98">cane</text>
    <polyline class="stroke-cane-light" points="112,70 78,70 78,96"/>
    <polygon class="fill-cane-light" points="67,94 89,94 78,108"/>

    <polygon class="fill-cane-light" points="14,115 141,115 169,144 141,173 14,173 42,144"/>
    <polygon class="fill-cane-mid" points="141,115 268,115 296,144 268,173 141,173 169,144"/>
    <polygon class="fill-cane-light" points="268,115 395,115 423,144 395,173 268,173 296,144"/>
    <polygon class="fill-cane-mid" points="395,115 522,115 550,144 522,173 395,173 423,144"/>
    <polygon class="fill-cane-light" points="522,115 649,115 677,144 649,173 522,173 550,144"/>

    <text class="stage-name" x="99" y="150" text-anchor="middle">Milling</text>
    <text class="stage-name" x="229" y="150" text-anchor="middle">Pre-treatment</text>
    <text class="stage-name" x="350" y="150" text-anchor="middle">Filteration</text>
    <text class="stage-name" x="480" y="150" text-anchor="middle">Fermentation</text>
    <text class="stage-name" x="601" y="150" text-anchor="middle">Distillation</text>

    <text class="label" x="683" y="121">Dehydration</text>
    <polygon class="fill-cane-mid" points="683,139 745,139 745,131 767,145 745,159 745,151 683,151"/>
    <text class="product product--cane" x="770" y="151">Ethanol</text>

    <polygon class="fill-cane-light" points="75,181 81,181 81,196 87,196 78,207 69,196 75,196"/>
    <text class="label" x="92" y="196">Bagasse</text>
    <text class="label" x="58" y="234">Boiler</text>

    <polygon class="fill-cane-light" points="325,181 331,181 331,196 337,196 328,207 319,196 325,196"/>
    <text class="label" x="316" y="234">Cake</text>

    <polygon class="fill-cane-mid" points="449,211 455,211 455,194 461,194 452,182 443,194 449,194"/>
    <text class="label" x="434" y="234">Yeast</text>
  </g>

  <!-- Corn route -->
  <g class="route route--corn">
    <text class="feed feed--corn" x="126" y="292">Dry ground</text>
    <text class="feed feed--corn" x="126" y="313">corn</text>
    <polyline class="stroke-corn-yellow" points="116,293 80,293 80,322"/>
    <polygon class="fill-corn-yellow" points="69,320 91,320 80,336"/>

    <polygon class="fill-corn-yellow" points="25,343 157,343 185,373 157,403 25,403 53,373"/>
    <polygon class="fill-corn-orange" points="157,343 289,343 317,373 289,403 157,403 185,373"/>
    <polygon class="fill-corn-yellow" points="289,343 421,343 449,373 421,403 289,403 317,373"/>
    <polygon class="fill-corn-orange" points="421,343 553,343 581,373 553,403 421,403 449,373"/>

    <text class="stage-name" x="108" y="379" text-anchor="middle">Milling</text>
    <text class="stage-name" x="245" y="379" text-anchor="middle">Liquefaction</text>
    <text class="stage-name" x="378" y="367" text-anchor="middle">Hydrolysis and</text>
    <text class="stage-name" x="376" y="388" text-anchor="middle">Fermentation</text>
    <text class="stage-name" x="507" y="379" text-anchor="middle">Distillation</text>

    <text class="label" x="598" y="353">Dehydration</text>
    <polygon class="fill-corn-yellow" points="598,368 666,368 666,360 690,374 666,388 666,380 598,380"/>
    <text class="product product--corn" x="698" y="380">Ethanol</text>

    <polygon class="fill-corn-orange" points="225,444 231,444 231,424 237,424 228,411 219,424 225,424"/>
    <text class="label" x="204" y="468">Enzyme</text>

    <polygon class="fill-corn-yellow" points="355,444 361,444 361,424 367,424 358,411 349,424 355,424"/>
    <text class="label" x="336" y="468">Enzyme</text>

    <polygon class="fill-corn-orange" points="487,410 493,410 493,430 499,430 490,443 481,430 487,430"/>
    <text class="label" x="472" y="471">Solids</text>

    <polygon class="fill-corn-orange" points="487,488 493,488 493,508 499,508 490,521 481,508 487,508"/>
    <text class="label" x="506" y="502">drying</text>
    <text class="label" x="430" y="545">Distillers Dry Grains</text>
  </g>

  <text class="caption" x="425" y="578" text-anchor="middle">Fig. 4.1.2: Stages in the production of bioethanol</text>
</svg>
</body>
</html>
```